Maple Roster Business Card for recruitment company

We are looking for a Business Card Design that incorporates our personal details and our busines name and logo. We are a specialized search consultancy that recruit Property and Construction professionals.
We would like a business card that stands out and is appealing to the Construction and Property industry as well.

Target Market(s)

people in the construction and property industry

Contact Information for Business Card

Business Name and logo

Font styles to use
Serif

Colors
0094D4
00A9DD
6FCCEA
C7EBF8
E9F6FB

Requirements
Must have
• Business name and logo as well as contact details
Should not have
• No photos of us please

```html
<!DOCTYPE html>
<html lang="en">
<head>
<meta charset="UTF-8">
<title>Maple Roster – Business Card</title>
<link href="https://fonts.googleapis.com/css2?family=Montserrat:wght@400;600&family=Playfair+Display:wght@400;700&display=swap" rel="stylesheet">
<style>
  :root {
    --backdrop: #d3d3d3;
    --card-white: #ffffff;
    --brand-navy: #043a4f;
    --name-navy: #0b3c54;
    --accent-blue: #0094d4;
    --accent-sky: #00a9dd;
    --accent-pale: #c7ebf8;
    --text-dark: #2a2a2a;
    --text-muted: #4a4a4a;
    --on-navy: #ffffff;
  }
  * { margin: 0; padding: 0; box-sizing: border-box; }
  html, body {
    width: 900px; height: 1200px; overflow: hidden;
    background: var(--backdrop);
    font-family: "Montserrat", Arial, sans-serif;
  }
  .canvas { position: relative; width: 900px; height: 1200px; }

  .card {
    position: absolute; left: 79px; width: 743px; height: 441px;
    box-shadow: 0 6px 18px rgba(0,0,0,0.28);
    overflow: hidden;
  }
  .card-front { top: 131px; background: var(--card-white); }
  .card-back { top: 638px; background: var(--brand-navy); }

  .front-band {
    position: absolute; left: 0; bottom: 0; width: 100%; height: 12px;
    background: var(--brand-navy);
  }

  .brand {
    position: absolute; display: flex; align-items: center; white-space: nowrap;
  }
  .brand-mark { border-radius: 50%; flex: none; }
  .wordmark {
    font-family: "Playfair Display", Georgia, serif;
    font-weight: 400; text-transform: uppercase; line-height: 1;
  }

  .card-front .brand { left: 46px; top: 58px; }
  .card-front .brand-mark { width: 30px; height: 30px; margin-right: 12px; background: var(--accent-blue); }
  .card-front .wordmark { font-size: 40px; letter-spacing: 1px; color: var(--brand-navy); }

  .card-back .brand { left: 0; right: 0; top: 192px; justify-content: center; }
  .card-back .brand-mark { width: 46px; height: 46px; margin-right: 18px; background: var(--accent-sky); }
  .card-back .wordmark { font-size: 62px; letter-spacing: 1.5px; color: var(--on-navy); }

  .person { position: absolute; left: 40px; top: 254px; }
  .person-name {
    font-family: "Playfair Display", Georgia, serif;
    font-size: 26px; font-weight: 700; color: var(--name-navy); line-height: 1.1;
  }
  .person-role { font-size: 16px; font-weight: 400; color: var(--text-muted); margin-top: 5px; }

  .divider {
    position: absolute; left: 40px; top: 314px; width: 647px; height: 1px;
    background: var(--accent-blue);
  }

  .contact-list { position: absolute; left: 40px; top: 330px; list-style: none; }
  .contact-item {
    display: flex; align-items: center; height: 24px;
    font-size: 16px; color: var(--text-dark);
  }
  .contact-icon { width: 14px; height: 14px; margin-right: 15px; margin-left: 1px; fill: var(--accent-blue); }

  .address {
    position: absolute; left: 506px; top: 358px;
    font-size: 16px; line-height: 21px; color: var(--text-dark); font-style: normal;
  }
</style>
</head>
<body>
<div class="canvas">

  <section class="card card-front">
    <div class="brand">
      <span class="brand-mark" role="img" aria-label="Maple Roster logo"></span>
      <span class="wordmark">Maple Roster</span>
    </div>

    <div class="person">
      <div class="person-name">Dana Whitlow</div>
      <div class="person-role">Owner/ Designer</div>
    </div>

    <div class="divider"></div>

    <ul class="contact-list">
      <li class="contact-item">
        <svg class="contact-icon" viewBox="0 0 16 16" aria-hidden="true">
          <path d="M2 5c0-2 2-3 6-3s6 1 6 3v1h-3V5H5v1H2z"/>
          <path d="M4 7h8l2 6H2z"/>
        </svg>
        (555) 014-2087
      </li>
      <li class="contact-item">
        <svg class="contact-icon" viewBox="0 0 16 16" aria-hidden="true">
          <path d="M1 4h14v1L8 9 1 5z"/>
          <path d="M1 6.5l7 4 7-4V13H1z"/>
        </svg>
        info@mapleroster.com
      </li>
      <li class="contact-item">
        <svg class="contact-icon" viewBox="0 0 16 16" aria-hidden="true">
          <circle cx="8" cy="8" r="7"/>
          <path d="M1.5 8h13M8 1.2c-2.4 2-2.4 11.6 0 13.6M8 1.2c2.4 2 2.4 11.6 0 13.6" stroke="#fff" stroke-width="1" fill="none"/>
        </svg>
        www.mapleroster.com
      </li>
    </ul>

    <address class="address">82 Harbor Lane<br>Cedar Point, CA 90000</address>

    <div class="front-band"></div>
  </section>

  <section class="card card-back">
    <div class="brand">
      <span class="brand-mark" role="img" aria-label="Maple Roster logo"></span>
      <span class="wordmark">Maple Roster</span>
    </div>
  </section>

</div>
</body>
</html>
```